Fresh, modern, fun business card for pediatric dental practice

Need a business card for fresh, modern, fun pediatric dental practice

Clean look that matches our website's font and colors

We prefer the look of curved corners on business cards

Target Market(s)

parents (mothers) of young children, professionals, mid-high class

Industry/Entity Type

Dental

Contact Information for Business Card

Maplebrook Pediatric Dentistry
482 Quarry Lane
Suite 517
Alder Creek, ZZ 00000
555.555.0193
www.maplebrookkidsdental.example

Mei-Ran Tsai, DMD
Corinne Walbeck, DMD
(we are working on our email address, but we would like that on the card as well)

Font styles to use
Sans Serif

Requirements
Must have
• All info; we would also like to make cards for individual staff members
• colors from our website and color palatte, attatched
• use same font and design as website for branding
Nice to have
• clean, simple card that has a pop of color
• we would like to see a few designs with our tag line "where smiles get brighter"
• we are not sure if we want to have it on there or not
• we would like to see a few designs incorporating the ribbon graphic on our website where the word WELCOME is

```html
<!DOCTYPE html>
<html lang="en">
<head>
<meta charset="utf-8">
<title>Maplebrook Pediatric Dentistry – Business Card</title>
<link rel="stylesheet" href="https://fonts.googleapis.com/css2?family=Roboto:wght@400;500&display=swap">
<style>
  :root {
    --backdrop: #e9e6e2;
    --card: #f4f3f1;
    --card-edge: #dcd9d5;
    --sun-orange: #e99a1f;
    --berry: #a51c5f;
    --band-text: #fbefe4;
    --ink: #3d3a3a;
  }
  * { margin: 0; padding: 0; box-sizing: border-box; }
  html, body {
    width: 1200px; height: 969px; overflow: hidden;
    background: var(--backdrop);
    font-family: "Roboto", Arial, sans-serif;
  }
  .card {
    position: absolute; left: 100px; top: 198px;
    width: 1000px; height: 572px;
    background: var(--card);
    border: 1px solid var(--card-edge);
    border-radius: 30px;
    overflow: hidden;
    box-shadow: 0 10px 30px rgba(0,0,0,0.08);
  }
  .brand {
    position: absolute; top: 118px; left: 0; width: 100%;
    display: flex; justify-content: center; align-items: center; gap: 18px;
  }
  .brand-dot {
    width: 34px; height: 34px; border-radius: 50%;
    background: var(--sun-orange);
  }
  .brand-name {
    font-weight: 500; font-size: 44px; color: var(--sun-orange);
    letter-spacing: 0.5px; white-space: nowrap;
  }
  .doctor-band {
    position: absolute; top: 303px; left: 0; width: 100%; height: 103px;
    background: linear-gradient(90deg, var(--sun-orange) 0%, var(--sun-orange) 44%, var(--berry) 56%, var(--berry) 100%);
    display: flex; align-items: center;
  }
  .doctor {
    flex: 1; text-align: center; white-space: nowrap;
    font-weight: 500; font-size: 32px; color: var(--band-text);
  }
  .contact {
    position: absolute; top: 440px; left: 0; width: 100%;
    text-align: center; color: var(--ink); font-size: 24px; line-height: 34px;
  }
  .contact-row { display: flex; justify-content: center; gap: 26px; }
  .contact-item { display: inline-flex; align-items: center; gap: 8px; white-space: nowrap; }
  .contact-item svg { width: 20px; height: 20px; }
</style>
</head>
<body>
  <div class="card">
    <div class="brand">
      <span class="brand-dot"></span>
      <span class="brand-name">Maplebrook Pediatric Dentistry</span>
    </div>

    <div class="doctor-band">
      <div class="doctor">Mei-Ran Tsai, DMD</div>
      <div class="doctor">Corinne Walbeck, DMD</div>
    </div>

    <div class="contact">
      <div class="contact-row">
        <span class="contact-item">
          <svg viewBox="0 0 24 24" aria-hidden="true"><path fill="#e99a1f" d="M6.6 10.8a15.1 15.1 0 0 0 6.6 6.6l2.2-2.2c.3-.3.7-.4 1-.2 1.1.4 2.3.6 3.6.6.6 0 1 .4 1 1V20c0 .6-.4 1-1 1A17 17 0 0 1 3 4c0-.6.4-1 1-1h3.5c.6 0 1 .4 1 1 0 1.3.2 2.5.6 3.6.1.3 0 .7-.2 1z"/></svg>
          555.555.0193
        </span>
        <span class="contact-item">
          <svg viewBox="0 0 24 24" aria-hidden="true"><circle cx="12" cy="12" r="9" fill="none" stroke="#e99a1f" stroke-width="2.4"/><path d="M3 12h18M12 3c3 3 3 15 0 18M12 3c-3 3-3 15 0 18" fill="none" stroke="#e99a1f" stroke-width="1.6"/></svg>
          www.maplebrookkidsdental.example
        </span>
      </div>
      <div>Maplebrook Pediatric Dentistry, 482 Quarry Lane</div>
      <div>Suite 517, Alder Creek, ZZ 00000</div>
    </div>
  </div>
</body>
</html>
```